Stationary and document suite for consultancy business in Australia called Talmera

I would like to get a suite of documents suitable for my new business called Talmera. I have included the original brief below, however have already selected a design for the logo. I would like to get:
Letter head - simple letter template with "V" logo embossed in background
Word document - standard format with "V" logo embossed in background
Proposal document - bolder pages with cover and back cover, include empty pages with footer as well as contents
Powerpoint presentation - open to ideas
Email signature - banner style or text, open to ideas
Brief that was given for logo (logo not required)
The name of the business is derived from the latin word for green ("Viridis") combined with "co" which is intended to represent a number of different words: collaborative, cooperative, coaching, collective,  construction, consulting, etc.
My objective for the brand is to represent a dynamic, progressive and collaborative business, where our people have fun and enjoy their work.
The objective of our business is to provide consultancy services to construction businesses, mainly aimed at building high performing teams and strategic growth. We will create learning and development tools that businesses can use to increase staff satisfaction and retention. Our future goal is to invest in decarbonisation and sustainability technology for use in the construction industry.
Our target market is construction business leaders and infrastructure owners, who operate road, rail and utility assets. We also want to present as a dynamic, progressive and fun place to work that will be attractive to new employees.

```html
<!DOCTYPE html>
<html lang="en">
<head>
<meta charset="utf-8">
<title>Talmera Stationery and Document Suite</title>
<link rel="stylesheet" href="https://fonts.googleapis.com/css2?family=Montserrat:wght@600;700&family=Open+Sans:ital,wght@0,400;0,600;1,400&family=Poppins:wght@300;400;500;600&display=swap">
<style>
:root{
  --board:#cfcfcf;
  --ink:#454547;
  --grey:#6f6f71;
  --soft:#a6a6a6;
  --green:#8dc63f;
  --paper:#ffffff;
  --mist:#eef3fb;
  --rule:#c9c9c9;
}
*{margin:0;padding:0;box-sizing:border-box}
html,body{width:816px;height:1200px;overflow:hidden;background:var(--board)}
.board{position:absolute;left:0;top:0;width:1500px;height:2206px;transform:scale(.544);transform-origin:0 0;font-family:"Open Sans",sans-serif;color:var(--ink)}
.sheet{position:absolute;background:var(--paper);overflow:hidden}
.caption{position:absolute;font:400 8.5px "Open Sans",sans-serif;letter-spacing:.4px;color:#222;text-transform:uppercase;transform:translateX(-50%);white-space:nowrap}
.wordmark{position:absolute;font-family:"Poppins",sans-serif;font-weight:400;color:var(--grey);line-height:1;letter-spacing:.5px}
.wordmark.light{color:var(--paper)}
.bar{position:absolute;left:0;right:0;bottom:0;height:7px;background:linear-gradient(100deg,var(--ink) 79%,var(--green) 79%)}
.contact{position:absolute;font-size:7px;line-height:8.6px;color:var(--grey)}
.contact p{display:flex;align-items:center;gap:4px}
.contact.right p{justify-content:flex-end}
.ico{display:inline-block;width:5px;height:5px;background:var(--green)}
.ico.round{border-radius:50%}
.contact.light{color:var(--paper)}

/* proposal */
.cover-front{background:var(--mist)}
.year{position:absolute;left:0;right:0;text-align:center;font:700 40px "Montserrat",sans-serif;color:var(--green)}
.report{position:absolute;left:0;right:0;text-align:center;font:700 40px/41px "Montserrat",sans-serif;letter-spacing:5px;color:var(--grey)}
.prep{position:absolute;left:0;right:0;text-align:center}
.prep .label{font:600 9.5px "Poppins",sans-serif;color:var(--green)}
.prep .name{font:500 15px "Poppins",sans-serif;color:#222;margin-top:8px}
.prep .role{font:italic 7px "Open Sans",sans-serif;margin-top:-2px}
.prep .date{font:400 10px "Poppins",sans-serif;margin-top:14px}
.disclaimer{position:absolute;left:30px;right:30px;text-align:center;font:italic 7.5px/10px "Open Sans",sans-serif;color:var(--grey)}
.dark{background:var(--ink)}
.thanks-title{position:absolute;font:600 17px "Poppins",sans-serif;color:var(--green)}
.page-head{position:absolute;left:29px;right:29px;top:30px;height:22px;border-bottom:1.5px solid var(--green)}
.page-head h2{font:600 13px "Poppins",sans-serif;color:var(--ink)}
.page-head h2 span{color:var(--green)}
.page-head .wordmark{right:0;top:-2px;font-size:15px}
.photo-fill{position:absolute;background:var(--soft)}
.body-copy{position:absolute;font-size:6.2px;line-height:8.3px;color:var(--grey);text-align:justify}
.body-copy p+p{margin-top:8px}
.page-foot{position:absolute;left:29px;right:29px;bottom:22px;border-top:1.5px solid var(--green);padding-top:5px;display:flex;justify-content:space-between;font:600 7px "Open Sans",sans-serif}

/* slides */
.slide{width:330px;height:247px}
.slide .head{position:absolute;left:17px;right:17px;top:20px;height:22px;border-bottom:1px solid var(--ink)}
.slide .head h3{font:600 14px/14px "Poppins",sans-serif;color:var(--green)}
.slide .head small{display:block;font-size:8px;line-height:9px;color:var(--ink)}
.slide .head .wordmark{right:0;top:6px;font-size:13px}
.slide .foot{position:absolute;left:17px;right:17px;bottom:22px;border-top:1.5px solid var(--green);padding-top:3px;display:flex;justify-content:space-between;font-size:6px;color:var(--ink)}
.slide .foot b{font-weight:600}
.title-block{position:absolute;right:34px;top:128px;text-align:right}
.title-block .wordmark{position:static;font-size:30px;margin-bottom:8px;color:var(--grey)}
.title-block .wordmark.light{color:var(--paper)}
.title-block .w{font:600 13px/14px "Poppins",sans-serif;color:var(--green)}
.title-block .n{font:500 13.5px/14px "Poppins",sans-serif;color:var(--paper)}
.title-block .d{font:italic 11px/13px "Open Sans",sans-serif;color:var(--green)}
.cover-light{background:linear-gradient(180deg,#ffffff,#e4e2e2)}
.cover-light .n{color:var(--grey)}
.toc{position:absolute;left:26px;right:28px;top:66px;list-style:none}
.toc li{display:flex;justify-content:space-between;font-size:8.5px;height:27.7px;padding-top:1px;border-bottom:.5px solid #ddd}
.toc li span:last-child{font-size:5px}
.team{position:absolute;top:60px;width:75px}
.team .photo{width:64px;height:64px;background:var(--ink);border:1px solid #999;color:#ddd;font-size:8px;display:flex;align-items:center;justify-content:center}
.team .who{font-size:6px;color:var(--green);margin-top:10px}
.team p{font-size:4.6px;line-height:5.6px;color:var(--grey)}
.team p+p{margin-top:8px}
.divider{position:absolute;top:62px;width:1px;height:110px;background:var(--rule)}
.bullets{position:absolute;left:24px;right:22px;top:66px;list-style:none}
.bullets li{position:relative;padding-left:7px;font-size:5px;line-height:6.6px;color:var(--grey);margin-bottom:9px}
.bullets li::before{content:"";position:absolute;left:0;top:2px;width:3px;height:3px;border-radius:50%;background:var(--green)}
.numbered{position:absolute;left:33px;right:34px;top:60px;list-style:none}
.numbered li{font-size:5px;line-height:6.6px;color:var(--grey);margin-bottom:8.5px}
.small-copy{position:absolute;font-size:4.8px;line-height:6.4px;color:var(--grey)}
.legend{position:absolute;font-size:4.6px;color:var(--grey)}
.legend p{display:flex;align-items:center;gap:4px;margin-bottom:3px}
.legend i{width:6px;height:6px;display:inline-block}
.thanks-big{position:absolute;right:36px;top:130px;text-align:right;font-family:"Poppins",sans-serif;font-weight:300}
.thanks-big .t{font-size:33px;line-height:32px;color:var(--green)}
.thanks-big .f{font-size:19px;line-height:20px;color:var(--paper)}

/* signatures */
.sig-name{font:600 9px "Poppins",sans-serif;color:var(--grey)}
.sig-role{font-size:7px;color:var(--green)}
</style>
</head>
<body>
<main class="board">

  <!-- Row 1: letterhead, word document, plain page, envelope -->
  <section class="sheet" style="left:82px;top:88px;width:323px;height:417px">
    <div class="wordmark" style="left:26px;top:30px;font-size:26px">Talmera</div>
    <div class="contact" style="left:220px;top:36px">
      <p><span class="ico round"></span>+61 400 555 018</p>
      <p><span class="ico"></span>rowan@talmera.com.au</p>
      <p><span class="ico round"></span>talmera.com.au</p>
    </div>
    <div class="bar"></div>
  </section>
  <span class="caption" style="left:246px;top:525px">Letter Head</span>

  <section class="sheet" style="left:435px;top:88px;width:322px;height:417px">
    <div class="wordmark" style="left:24px;top:30px;font-size:26px">Talmera</div>
    <div class="contact" style="left:217px;top:36px">
      <p><span class="ico round"></span>+61 400 555 018</p>
      <p><span class="ico"></span>rowan@talmera.com.au</p>
      <p><span class="ico round"></span>talmera.com.au</p>
    </div>
    <div class="bar"></div>
  </section>
  <span class="caption" style="left:599px;top:525px">Word Document</span>

  <section class="sheet" style="left:788px;top:88px;width:322px;height:417px">
    <div class="wordmark" style="left:22px;top:28px;font-size:20px">Talmera</div>
    <div class="bar"></div>
  </section>

  <section class="envelope">
    <div class="sheet" style="left:1034px;top:132px;width:323px;height:146px;background:#f4f4f4">
      <svg width="323" height="48" style="position:absolute;left:0;top:0" aria-hidden="true">
        <path d="M0 0H323L315 36Q312 46 300 46H23Q11 46 8 36Z" fill="var(--ink)"/>
      </svg>
      <div class="wordmark light" style="left:128px;top:16px;font-size:18px">Talmera</div>
    </div>
    <div class="sheet" style="left:1017px;top:200px;width:326px;height:148px">
      <div class="wordmark" style="left:18px;top:22px;font-size:18px">Talmera</div>
      <div class="bar"></div>
    </div>
  </section>
  <span class="caption" style="left:1238px;top:361px">Envelope Front &amp; Back</span>

  <!-- Row 2: proposal -->
  <section class="sheet cover-front" style="left:82px;top:566px;width:322px;height:455px">
    <div class="wordmark" style="left:48px;top:70px;font-size:56px">Talmera</div>
    <div class="year" style="top:152px">2022</div>
    <div class="report" style="top:198px">ANNUAL<br>REPORT</div>
    <div class="prep" style="top:298px">
      <div class="label">PREPARED BY</div>
      <div class="name">ELLIS WARREN</div>
      <div class="role">Managing Director</div>
      <div class="date">15, JUNE, 2022</div>
    </div>
    <p class="disclaimer" style="top:412px">Prepared for internal review. Figures shown are indicative and subject to final audit before release to stakeholders.</p>
    <div class="bar"></div>
  </section>
  <span class="caption" style="left:230px;top:1040px">Proposal Front</span>

  <section class="sheet dark" style="left:434px;top:566px;width:321px;height:455px">
    <div class="thanks-title" style="right:42px;top:368px">Thank You</div>
    <div class="contact right light" style="right:42px;top:396px">
      <p>+61 400 555 018<span class="ico round"></span></p>
      <p>rowan@talmera.com.au<span class="ico"></span></p>
      <p>talmera.com.au<span class="ico round"></span></p>
    </div>
  </section>
  <span class="caption" style="left:582px;top:1040px">Proposal Back</span>

  <section class="sheet" style="left:788px;top:566px;width:321px;height:455px">
    <header class="page-head">
      <h2>ABOUT <span>US</span></h2>
      <div class="wordmark">Talmera</div>
    </header>
    <div class="photo-fill" role="img" aria-label="Feature photograph for the About Us page" style="left:30px;top:72px;width:262px;height:175px"></div>
    <div class="body-copy" style="left:30px;top:253px;width:262px">
      <p>Talmera works alongside construction leaders to build teams that perform, grow and stay. We listen first, map what is working, and shape practical plans that people can carry forward long after our work on site has wrapped up and the next project begins.</p>
      <p>Our programs blend coaching, workshops and simple tools that crews and managers can use every week. Each engagement starts with clear goals, honest feedback and a shared view of success. We measure progress together, adjust as conditions change and keep the focus on the people who deliver road, rail and utility assets across the country every day of the year.</p>
      <p>We also invest in cleaner methods and smarter materials to help the industry cut carbon.</p>
    </div>
    <footer class="page-foot"><span>TALMERA.COM.AU</span><span>1</span></footer>
  </section>
  <span class="caption" style="left:936px;top:1037px">Proposal Inner</span>

  <!-- Row 3: presentation -->
  <section class="sheet slide dark" style="left:61px;top:1093px">
    <div class="title-block">
      <div class="wordmark light">Talmera</div>
      <div class="w">Welcome to Our</div>
      <div class="n">PRESENTATION NAME</div>
      <div class="d">Description</div>
    </div>
  </section>

  <section class="sheet slide cover-light" style="left:412px;top:1093px">
    <div class="title-block">
      <div class="wordmark">Talmera</div>
      <div class="w">Welcome to Our</div>
      <div class="n">PRESENTATION NAME</div>
      <div class="d">Description</div>
    </div>
  </section>

  <section class="sheet slide" style="left:764px;top:1093px">
    <header class="head"><h3>CONTENTS</h3><small>Sub Heading</small><div class="wordmark">Talmera</div></header>
    <ol class="toc">
      <li><span>&nbsp;I&nbsp; ABOUT US</span><span>2</span></li>
      <li><span>&nbsp;II&nbsp; OUR SERVICES</span><span>3</span></li>
      <li><span>&nbsp;III&nbsp; CASE STUDY</span><span>4</span></li>
      <li><span>&nbsp;IV&nbsp; DIAGRAM</span><span>5</span></li>
      <li><span>&nbsp;V&nbsp; CONTACTS</span><span>6</span></li>
    </ol>
    <footer class="foot"><span>www.<b>talmera</b>.com.au</span><span>PAGE1</span></footer>
  </section>

  <!-- Row 4 -->
  <section class="sheet slide" style="left:61px;top:1372px">
    <header class="head"><h3>ABOUT US</h3><small>Sub Heading</small><div class="wordmark">Talmera</div></header>
    <div class="team" style="left:30px">
      <div class="photo" role="img" aria-label="Team member portrait">Photo</div>
      <div class="who">Team Member</div>
      <p>Role title and short profile</p>
      <p>Brief background covering skills, projects and the value this person brings to every client.</p>
    </div>
    <div class="divider" style="left:110px"></div>
    <div class="team" style="left:127px">
      <div class="photo" role="img" aria-label="Team member portrait">Photo</div>
      <div class="who">Team Member</div>
      <p>Role title and short profile</p>
      <p>Brief background covering skills, projects and the value this person brings to every client.</p>
    </div>
    <div class="divider" style="left:210px"></div>
    <div class="team" style="left:227px">
      <div class="photo" role="img" aria-label="Team member portrait">Photo</div>
      <div class="who">Team Member</div>
      <p>Role title and short profile</p>
      <p>Brief background covering skills, projects and the value this person brings to every client.</p>
    </div>
    <footer class="foot"><span>www.<b>talmera</b>.com.au</span><span>PAGE1</span></footer>
  </section>

  <section class="sheet slide" style="left:412px;top:1372px">
    <header class="head"><h3>BULLET TEXT</h3><small>Sub Heading</small><div class="wordmark">Talmera</div></header>
    <ul class="bullets">
      <li>Strong teams start with clear roles, shared goals and leaders who make time to listen to the people doing the work.</li>
      <li>Regular coaching sessions help site managers turn feedback into action and build trust across crews, designers and clients on every project.</li>
      <li>Simple learning tools give staff a way to grow skills between projects, which lifts satisfaction and keeps good people in the business.</li>
      <li>Growth plans are built around real data from your operations so every decision links back to measurable outcomes and owners.</li>
      <li>Cleaner materials and smarter methods reduce carbon on road, rail and utility assets while lowering long term running costs.</li>
    </ul>
    <footer class="foot"><span>www.<b>talmera</b>.com.au</span><span>PAGE1</span></footer>
  </section>

  <section class="sheet slide" style="left:764px;top:1372px">
    <header class="head"><h3>CASE STUDY</h3><small>Sub Heading</small><div class="wordmark">Talmera</div></header>
    <svg style="position:absolute;left:36px;top:60px" width="130" height="104" aria-label="Bar chart of four results">
      <g stroke="#e2e2e2" stroke-width=".5">
        <line x1="0" y1="4" x2="130" y2="4"/><line x1="0" y1="24" x2="130" y2="24"/><line x1="0" y1="44" x2="130" y2="44"/><line x1="0" y1="64" x2="130" y2="64"/><line x1="0" y1="84" x2="130" y2="84"/><line x1="0" y1="103" x2="130" y2="103"/>
      </g>
      <g fill="var(--green)">
        <rect x="30" y="6" width="15" height="97"/><rect x="48" y="20" width="15" height="83"/><rect x="66" y="42" width="15" height="61"/><rect x="84" y="28" width="15" height="75"/>
      </g>
      <g fill="#fff" font-size="5" font-family="Open Sans, sans-serif">
        <text transform="translate(40 98) rotate(-90)">Sub head1</text><text transform="translate(58 98) rotate(-90)">Sub head2</text><text transform="translate(76 98) rotate(-90)">Sub head3</text><text transform="translate(94 98) rotate(-90)">Sub head4</text>
      </g>
    </svg>
    <div class="small-copy" style="left:198px;top:64px;width:110px">Crews reported higher engagement within six months. Turnover fell and project handovers ran on schedule.<br>Leaders adopted weekly check ins and shared dashboards.<br>Training hours doubled across all sites and regions.</div>
    <div class="small-copy" style="left:30px;top:176px;width:272px">A regional rail contractor partnered with us to rebuild team structure after rapid growth. Together we set clear roles, coached supervisors and introduced simple tools for feedback. Results improved steadily across safety, delivery and staff retention measures.</div>
    <footer class="foot"><span>www.<b>talmera</b>.com.au</span><span>PAGE1</span></footer>
  </section>

  <!-- Row 5 -->
  <section class="sheet slide" style="left:61px;top:1651px">
    <header class="head"><h3>DIAGRAM</h3><small>Sub Heading</small><div class="wordmark">Talmera</div></header>
    <div class="small-copy" style="left:30px;top:72px;width:138px;text-align:center">Our approach moves through four stages that repeat as teams mature. We begin by listening, then define goals with leaders, coach people through change and finally measure results. Each stage feeds the next so progress compounds over time. Clients see gains in engagement, retention and delivery, and the tools stay with the business long after each engagement ends.</div>
    <div class="small-copy" style="left:30px;top:164px;width:138px;text-align:center">Stages can be tailored to suit project size, team structure and the goals set by each client.</div>
    <svg style="position:absolute;left:208px;top:60px" width="76" height="76" aria-label="Pie chart">
      <circle cx="38" cy="38" r="36" fill="var(--green)"/>
      <path d="M38 38L38 2A36 36 0 0 1 71 24Z" fill="var(--grey)"/>
      <path d="M38 38L74 40A36 36 0 0 1 56 69Z" fill="var(--grey)"/>
      <path d="M38 38L71 24A36 36 0 0 1 74 40Z" fill="var(--green)" stroke="#fff" stroke-width="1"/>
      <g stroke="#fff" stroke-width="1.2"><line x1="38" y1="38" x2="38" y2="2"/><line x1="38" y1="38" x2="71" y2="24"/><line x1="38" y1="38" x2="56" y2="69"/></g>
    </svg>
    <div class="legend" style="left:208px;top:148px">
      <p><i style="background:var(--green)"></i>Coaching and training 50%</p>
      <p><i style="background:var(--grey)"></i>Strategy and growth 50%</p>
    </div>
    <div class="small-copy" style="left:206px;top:176px;width:100px">Share of client hours by service area this year.</div>
    <footer class="foot"><span>www.<b>talmera</b>.com.au</span><span>PAGE1</span></footer>
  </section>

  <section class="sheet slide" style="left:412px;top:1651px">
    <header class="head"><h3>OUR SERVICES</h3><small>Sub Heading</small><div class="wordmark">Talmera</div></header>
    <ol class="numbered">
      <li>1. Team health checks for site crews.</li>
      <li>2. Leadership coaching for managers and supervisors on live projects.</li>
      <li>3. Strategic growth planning that links business goals to people, capability and the resources needed to deliver them.</li>
      <li>4. Learning and development tools that staff can use between projects to build skills, confidence and career paths.</li>
      <li>5. Workshops that bring designers, builders and asset owners together to solve problems early, share lessons and agree clear ways of working before work starts on site.</li>
      <li>6. Sustainability advice on lower carbon materials, methods and technology for road, rail and utility assets, with practical steps that fit each project budget and timeline.</li>
    </ol>
    <footer class="foot"><span>www.<b>talmera</b>.com.au</span><span>PAGE1</span></footer>
  </section>

  <section class="sheet slide dark" style="left:764px;top:1651px">
    <div class="thanks-big"><div class="t">Thanks</div><div class="f">For Coming</div></div>
    <div class="contact right light" style="right:38px;top:196px;font-size:6.5px;line-height:8px">
      <p>+61 400 555 018<span class="ico round"></span></p>
      <p>rowan@talmera.com.au<span class="ico"></span></p>
      <p>talmera.com.au<span class="ico round"></span></p>
    </div>
  </section>

  <!-- Row 6: email signatures -->
  <section class="sheet" style="left:179px;top:1983px;width:321px;height:93px">
    <div class="wordmark" style="left:42px;top:26px;font-size:30px">Talmera</div>
    <div style="position:absolute;left:178px;top:18px">
      <div class="sig-name">ROWAN PETRIE</div>
      <div class="sig-role">Director</div>
    </div>
    <div class="contact" style="left:180px;top:43px">
      <p><span class="ico round"></span>+61 400 555 018</p>
      <p><span class="ico"></span>rowan@talmera.com.au</p>
      <p><span class="ico round"></span>talmera.com.au</p>
    </div>
    <svg style="position:absolute;left:0;bottom:0" width="321" height="22" aria-hidden="true">
      <path d="M0 4Q160 22 321 6V22H0Z" fill="var(--ink)"/>
      <path d="M0 2Q160 16 321 4V8Q160 20 0 6Z" fill="var(--green)"/>
    </svg>
  </section>
  <span class="caption" style="left:338px;top:2087px">Email Signature 01</span>

  <section class="sheet" style="left:632px;top:1994px;width:323px;height:63px">
    <div class="wordmark" style="left:16px;top:22px;font-size:20px">Talmera</div>
    <div style="position:absolute;left:103px;top:22px">
      <div class="sig-name">ROWAN PETRIE</div>
      <div class="sig-role">Director</div>
    </div>
    <div class="contact" style="left:230px;top:19px">
      <p><span class="ico round"></span>+61 400 555 018</p>
      <p><span class="ico"></span>rowan@talmera.com.au</p>
      <p><span class="ico round"></span>talmera.com.au</p>
    </div>
  </section>
  <span class="caption" style="left:794px;top:2092px">Email Signature 02</span>

</main>
</body>
</html>
```